Business Card Design For A Renovation Contractor Company

We need a business card for a new company based in Singapore, our company name is "RB Tolvane". We are a renovation contractor that builds designs into reality. We build more of F&B restaurants, retail stores and commercial offices. We work very closely with designers. The final design should communicate to our client that we are a company that you can trust, that will plan and complete your project without giving you a headache. I like my client to remember my company as "RB". The beauty of SIMPLE is important.

Industry/Entity Type

Contractor

Requirements
Nice to have
• Black or Red base

```html
<!DOCTYPE html>
<html lang="en">
<head>
<meta charset="utf-8">
<title>RB Tolvane – Business Card</title>
<link rel="stylesheet" href="https://fonts.googleapis.com/css2?family=Questrial&family=Open+Sans:wght@400;700&display=swap">
<style>
  :root {
    --backdrop: #ecebe8;
    --card: #ffffff;
    --ink: #1a1a1a;
    --band: #111111;
    --accent: #d3222a;
    --muted: #8a8a8a;
    --faint: #f1e6e7;
    --band-text: #f2f2f2;
  }
  * { box-sizing: border-box; margin: 0; padding: 0; }
  html, body {
    width: 1200px; height: 720px; overflow: hidden;
    background: var(--backdrop);
    font-family: "Questrial", "Open Sans", sans-serif;
    color: var(--ink);
  }
  .canvas {
    position: relative; width: 1200px; height: 720px;
    display: flex; align-items: center; justify-content: center; gap: 50px;
  }
  .card {
    position: relative; width: 540px; height: 310px;
    background: var(--card);
    box-shadow: 0 2px 10px rgba(0,0,0,.12);
    overflow: hidden;
  }

  /* Front: contact side */
  .front .brand {
    position: absolute; top: 30px; left: 0; right: 0;
    display: flex; flex-direction: column; align-items: center;
  }
  .brand-mark {
    width: 46px; height: 46px; border-radius: 50%;
    border: 5px solid var(--ink); margin-bottom: 10px;
  }
  .brand-name {
    font-size: 40px; line-height: 1; color: var(--ink); letter-spacing: -0.5px;
  }
  .tagline {
    font-size: 15px; color: var(--ink); letter-spacing: .4px;
    border-top: 1.5px solid var(--ink); padding-top: 2px; margin-top: 4px;
  }
  .person {
    margin-top: 10px; font-family: "Open Sans", sans-serif; font-size: 15px;
  }
  .person .name { font-weight: 700; }
  .person .title { color: var(--accent); font-weight: 400; }
  .front .rule {
    position: absolute; left: 0; right: 0; top: 186px;
    height: 2px; background: var(--accent);
  }
  .band {
    position: absolute; left: 0; right: 0; top: 194px; bottom: 0;
    background: var(--band); color: var(--band-text);
    display: flex; align-items: center; justify-content: center;
    font-family: "Open Sans", sans-serif; font-size: 12px; line-height: 1.5;
  }
  .band::after {
    content: ""; position: absolute; left: 0; right: 0; bottom: 8px;
    height: 2px; background: var(--accent);
  }
  .address { text-align: right; padding-right: 16px; font-style: normal; }
  .divider { width: 1px; height: 70px; background: var(--muted); }
  .contacts { list-style: none; padding-left: 16px; }
  .contacts li { display: flex; align-items: center; gap: 7px; }
  .contacts svg { width: 11px; height: 11px; fill: var(--band-text); }

  /* Back: brand side */
  .back .halo {
    position: absolute; left: 180px; top: 40px;
    width: 200px; height: 200px; border-radius: 50%;
    border: 22px solid var(--faint);
  }
  .back .lockup {
    position: absolute; left: 0; right: 0; top: 100px;
    display: flex; flex-direction: column; align-items: center;
  }
  .back .brand-name { font-size: 54px; }
  .back .tagline { font-size: 19px; }
  .web {
    position: absolute; left: 0; right: 0; bottom: 36px; text-align: center;
    font-size: 15px; letter-spacing: 3px; color: var(--ink);
  }
  .web .accent { color: var(--accent); }
</style>
</head>
<body>
<main class="canvas">

  <section class="card front" aria-label="Card front, contact details">
    <div class="brand">
      <span class="brand-mark" aria-hidden="true"></span>
      <div class="brand-name">RB Tolvane</div>
      <div class="tagline">turning designs into spaces</div>
      <div class="person"><span class="name">Your Name,</span> <span class="title">Title</span></div>
    </div>
    <div class="rule"></div>
    <div class="band">
      <address class="address">
        Street Name<br>City Name<br>State Zip Code
      </address>
      <span class="divider"></span>
      <ul class="contacts">
        <li><svg viewBox="0 0 24 24"><path d="M6.6 10.8a15 15 0 0 0 6.6 6.6l2.2-2.2a1 1 0 0 1 1-.25 11.4 11.4 0 0 0 3.6.6 1 1 0 0 1 1 1V20a1 1 0 0 1-1 1A17 17 0 0 1 3 4a1 1 0 0 1 1-1h3.5a1 1 0 0 1 1 1c0 1.25.2 2.45.6 3.6a1 1 0 0 1-.25 1z"/></svg>123-456-0789</li>
        <li><svg viewBox="0 0 24 24"><path d="M7 1h10a2 2 0 0 1 2 2v18a2 2 0 0 1-2 2H7a2 2 0 0 1-2-2V3a2 2 0 0 1 2-2zm0 3v14h10V4zm5 15.5a1 1 0 1 0 0 2 1 1 0 0 0 0-2z"/></svg>123-456-0789</li>
        <li><svg viewBox="0 0 24 24"><path d="M2 5h20v14H2zm2 2v.5l8 5 8-5V7zm0 2.8V17h16V9.8l-8 5z"/></svg>info@rbtolvane.com</li>
        <li><svg viewBox="0 0 24 24"><path d="M12 2a10 10 0 1 0 0 20 10 10 0 0 0 0-20zm6.9 9h-3a15 15 0 0 0-1.3-5.6A8 8 0 0 1 18.9 11zM12 4.1c.9 1.2 1.8 3.6 1.9 6.9h-3.8c.1-3.3 1-5.7 1.9-6.9zM9.4 5.4A15 15 0 0 0 8.1 11h-3a8 8 0 0 1 4.3-5.6zM5.1 13h3a15 15 0 0 0 1.3 5.6A8 8 0 0 1 5.1 13zm6.9 6.9c-.9-1.2-1.8-3.6-1.9-6.9h3.8c-.1 3.3-1 5.7-1.9 6.9zm2.6-1.3a15 15 0 0 0 1.3-5.6h3a8 8 0 0 1-4.3 5.6z"/></svg>www.rbtolvane.com</li>
      </ul>
    </div>
  </section>

  <section class="card back" aria-label="Card back, brand side">
    <span class="halo" aria-hidden="true"></span>
    <div class="lockup">
      <div class="brand-name">RB Tolvane</div>
      <div class="tagline">turning designs into spaces</div>
    </div>
    <div class="web">www.<span class="accent">rbtolvane</span>.com</div>
  </section>

</main>
</body>
</html>
```